Innovative Web Application Welcome Page with Free Trial and Embedded Video

We run the Kestrel Defence Orchestration Suite (https://kestrel.marrowbyte.example), which is the world's first security automation cloud that delivers automated security to organisations.Our existing Welcome page (page shown after login) needs redesigning to be inline with our new Kestrel brand (i.e. the Kestrel website - innovative and global). The Welcome Page will promote a 30-day trial of our Proactive Breached Login Sentinel feature. Screenshots attached including current Welcome Page, mock up of new Welcome Page content, Kestrel logos, Kestrel brochures, Kestrel main brand hero image, slide images, etc. The application header and side menu must remain the same. The design is for the main section of this page.

Target Market(s)

IT Security

Number of Pages Required

1 page

Font styles to use
Sans Serif
Other font styles liked:
• Website creative specifications sheet attached

Colors

Designer to choose only greyscale colors for use in the design.

Requirements
Must have
• All sections and text in the mockup image provided

```html
<!DOCTYPE html>
<html lang="en">
<head>
<meta charset="utf-8">
<title>Kestrel Defence Orchestration Suite – Welcome</title>
<link href="https://fonts.googleapis.com/css2?family=Montserrat:wght@300;400;500;600;700&display=swap" rel="stylesheet">
<style>
  :root{
    --red:#e0282a;
    --red-dark:#8f1d1f;
    --black:#0d0d0f;
    --header:#1b2128;
    --sidebar:#2b3138;
    --sidebar-active:#22272d;
    --sidebar-text:#8a929b;
    --white:#ffffff;
    --ink:#1a1a1a;
    --body:#3a3a3a;
    --ring-grey:#d4d4d4;
  }
  *{box-sizing:border-box;margin:0;padding:0}
  html,body{width:889px;height:1200px;overflow:hidden}
  body{position:relative;background:var(--white);font-family:"Montserrat",sans-serif;color:var(--ink)}
  .abs{position:absolute}

  /* app header */
  .app-header{left:0;top:0;width:889px;height:50px;background:var(--header)}
  .app-brand{left:64px;top:13px;color:var(--white);font-size:20px;font-weight:400;letter-spacing:.5px}
  .app-menu{top:18px;color:var(--white);font-size:10px;font-weight:500}
  .app-menu svg{margin-left:16px;vertical-align:middle}

  /* side menu */
  .side-menu{left:0;top:50px;width:185px;height:1150px;background:var(--sidebar)}
  .side-art{left:0;top:50px;width:185px;height:122px;background:linear-gradient(135deg,#6b6e72 0%,#3d4045 45%,#7a1d1e 60%,#2b3138 100%)}
  .side-user{left:0;top:140px;width:28px;height:22px;background:var(--sidebar);color:var(--white);font-size:11px;font-weight:600;padding:4px 0 0 13px;width:40px}
  .side-active{left:0;top:175px;width:185px;height:34px;background:var(--sidebar-active)}
  .nav-item{left:15px;width:160px;height:16px;color:var(--sidebar-text);font-size:9.5px;display:flex;align-items:center}
  .nav-item.is-active{color:var(--white)}
  .nav-item .ico{width:11px;height:11px;border:1.2px solid currentColor;border-radius:2px;margin-right:14px}
  .nav-item .chev{margin-left:auto}
  .collapse-btn{left:142px;top:631px;width:43px;height:22px;background:#1b2026;border-radius:11px 0 0 11px;color:var(--white);font-size:13px;text-align:center;line-height:20px}

  /* hero */
  .hero{left:185px;top:50px;width:704px;height:225px;overflow:hidden}
  .hero-kicker{left:300px;top:136px;width:113px;text-align:right;color:var(--white);font-size:15.5px;font-weight:300;line-height:18px}
  .hero-brand{left:420px;top:112px;color:var(--white);font-size:68px;font-weight:300;letter-spacing:-1px}
  .hero-tag{left:513px;top:198px;color:var(--white);font-size:9.5px;letter-spacing:.8px;font-weight:400}
  .social{width:34px;height:34px;border-radius:50%;background:var(--white);top:228px}

  /* intro */
  .eyebrow{color:var(--red);font-size:9px;font-weight:600;letter-spacing:.2px}
  .title{font-size:18.5px;font-weight:400;letter-spacing:.2px;color:var(--ink);line-height:21px}
  .title em{font-style:normal;font-weight:700;color:var(--red)}
  .copy{font-size:9.5px;line-height:13px;color:var(--body)}
  .copy b{font-weight:600;color:var(--red)}
  .copy strong{font-weight:600;color:var(--ink)}
  .text-link{color:var(--red);font-size:8.5px;font-weight:600;letter-spacing:.3px}
  .text-link span{margin-left:10px;font-size:10px}
  .shield-art{left:701px;top:357px;width:119px;height:110px;border-radius:8px;background:radial-gradient(circle at 55% 50%,var(--red) 0%,#f0b0b0 55%,#fff 75%)}

  /* stat */
  .stat-value{left:218px;top:584px;width:160px;text-align:center;color:var(--red);font-size:41px;font-weight:600}
  .stat-label{left:218px;top:640px;width:160px;text-align:center;font-size:7.5px;color:var(--ink);letter-spacing:.1px}
  .btn{height:30px;display:flex;align-items:center;justify-content:center;font-size:7.5px;font-weight:600;letter-spacing:.2px;border-radius:3px}
  .btn-red{background:var(--red);color:var(--white);border:1px solid #b51d1f}
  .btn-white{background:var(--white);color:var(--ink)}

  /* trial banner */
  .trial-banner{left:185px;top:762px;width:704px;height:161px;background:linear-gradient(90deg,#5e1415 0%,#a42224 45%,#6c6c6c 80%,#3a3a3a 100%)}
  .trial-title{left:257px;top:795px;color:var(--white);font-size:18px;font-weight:400}
  .trial-title em{font-style:normal;font-weight:700}
  .trial-sub{left:257px;top:824px;color:var(--white);font-size:9.5px}
  .trial-sub b{font-weight:600}
  .trial-brand{left:777px;top:900px;color:var(--white);font-size:16px;font-weight:400}

  /* video */
  .video-thumb{left:576px;top:994px;width:248px;height:137px;background:linear-gradient(110deg,#d9d9d9 0%,#6d6d6d 35%,#1a1a1a 60%,#050505 100%)}
  .video-play{left:686px;top:1036px;width:30px;height:30px;border-radius:50%;background:var(--red)}
  .video-caption{left:610px;top:1110px;color:var(--white);font-size:8px;letter-spacing:.4px}
  .video-brand{left:730px;top:1097px;color:var(--white);font-size:24px;font-weight:400}
</style>
</head>
<body>

<!-- application header -->
<header class="abs app-header"></header>
<div class="abs app-brand">Kestrel</div>
<div class="abs app-menu" style="left:715px">Al<svg width="8" height="5" viewBox="0 0 8 5"><path d="M1 1l3 3 3-3" fill="none" stroke="#fff" stroke-width="1.3"/></svg></div>
<div class="abs app-menu" style="left:781px">US<svg width="8" height="5" viewBox="0 0 8 5"><path d="M1 1l3 3 3-3" fill="none" stroke="#fff" stroke-width="1.3"/></svg></div>

<!-- side menu -->
<nav class="abs side-menu" aria-label="Application menu"></nav>
<div class="abs side-art" role="img" aria-label="Abstract red and grey brand artwork"></div>
<div class="abs side-user">Al</div>
<div class="abs side-active"></div>
<div class="abs nav-item is-active" style="top:184px"><i class="ico" style="border-radius:50%"></i>Automation<span class="chev">›</span></div>
<div class="abs nav-item" style="top:225px"><i class="ico"></i>Marketplace<span class="chev">›</span></div>
<div class="abs nav-item" style="top:276px"><i class="ico"></i>Workflows<span class="chev">›</span></div>
<div class="abs nav-item" style="top:319px"><i class="ico" style="border-radius:50%"></i>Modules<span class="chev">›</span></div>
<div class="abs nav-item" style="top:362px"><i class="ico"></i>Services</div>
<div class="abs nav-item" style="top:405px"><i class="ico"></i>Containers<span class="chev">›</span></div>
<div class="abs nav-item" style="top:447px"><i class="ico"></i>Dashboard</div>
<div class="abs nav-item" style="top:489px"><i class="ico"></i>Charts<span class="chev">›</span></div>
<div class="abs collapse-btn">«</div>

<!-- hero -->
<section class="abs hero">
  <svg width="704" height="225" viewBox="0 0 704 225">
    <rect width="704" height="225" fill="var(--black)"/>
    <polygon points="0,0 242,0 344,225 0,225" fill="var(--red)"/>
  </svg>
</section>
<div class="abs hero-kicker">GETTING<br>STARTED<br>WITH</div>
<div class="abs hero-brand">Kestrel</div>
<div class="abs hero-tag">SECURITY AUTOMATION</div>
<div class="abs social" style="left:695px" aria-label="Social link"></div>
<div class="abs social" style="left:742px" aria-label="Social link"></div>
<div class="abs social" style="left:790px" aria-label="Social link"></div>

<!-- welcome -->
<div class="abs eyebrow" style="left:205px;top:355px">PRODUCT STARTER</div>
<h1 class="abs title" style="left:205px;top:371px">WELCOME TO <em>KESTREL SECURITY AUTOMATION</em></h1>
<p class="abs copy" style="left:205px;top:405px;width:400px"><b>Kestrel Breached Login Sentinel</b> helps to mitigate the #1 cyber security<br>threat through automation: <strong>Leaked Passwords.</strong></p>
<div class="abs text-link" style="left:205px;top:457px">LEARN HOW<span>»</span></div>
<div class="abs shield-art" role="img" aria-label="Illustration of a security shield with a tick on a circuit background"></div>

<!-- stat -->
<svg class="abs" style="left:204px;top:521px" width="188" height="188" viewBox="0 0 188 188" aria-label="95 percent ring chart">
  <circle cx="94" cy="94" r="83" fill="none" stroke="var(--ring-grey)" stroke-width="11"/>
  <circle cx="94" cy="94" r="83" fill="none" stroke="var(--red)" stroke-width="11"
          stroke-dasharray="339 521" transform="rotate(-90 94 94)"/>
</svg>
<div class="abs stat-value">95%</div>
<div class="abs stat-label">SECURITY BREACHES WORLDWIDE</div>

<h2 class="abs title" style="left:451px;top:563px">DID YOU <em>KNOW?</em></h2>
<p class="abs copy" style="left:451px;top:592px;width:380px;font-size:9px;line-height:12px">Most of the organizations with no security automation suffer <b>95% higher losses</b> from security breaches all over the world.</p>
<div class="abs btn btn-red" style="left:451px;top:634px;width:121px">GET FREE TRIAL NOW</div>

<!-- trial banner -->
<section class="abs trial-banner" role="img" aria-label="Dark red and grey photographic brand banner"></section>
<h2 class="abs trial-title">START YOUR <em>FREE 1 MONTH TRIAL NOW</em></h2>
<p class="abs trial-sub">Use <b>Kestrel Automation Trial Pack</b> to reveal your compromised accounts today.</p>
<div class="abs btn btn-red" style="left:257px;top:864px;width:120px">GET FREE TRIAL NOW</div>
<div class="abs btn btn-white" style="left:384px;top:864px;width:127px">READ OUR BROCHURES</div>
<div class="abs trial-brand">Kestrel</div>

<!-- getting started -->
<div class="abs eyebrow" style="left:210px;top:994px">GETTING STARTED:</div>
<h2 class="abs title" style="left:210px;top:1010px;width:360px">KESTREL PROACTIVE BREACHED<br>LOGIN SENTINEL</h2>
<p class="abs copy" style="left:210px;top:1057px;width:330px;font-size:9px;line-height:13px">Visit the <b>Kestrel Solution page</b> for more information, features, pricing, FAQs and Getting Started Guide.</p>
<div class="abs text-link" style="left:210px;top:1114px">KNOW MORE<span>»</span></div>

<div class="abs video-thumb" role="img" aria-label="Video thumbnail: getting started with Kestrel, brand photograph"></div>
<div class="abs video-play" aria-label="Play video"></div>
<svg class="abs" style="left:697px;top:1045px" width="11" height="12" viewBox="0 0 11 12"><path d="M0 0l11 6-11 6z" fill="#fff"/></svg>
<div class="abs video-caption">GETTING STARTED WITH</div>
<div class="abs video-brand">Kestrel</div>

</body>
</html>
```